Automotive component supplier needs a business card design

We need a business card design for our company called Velran Global Components Ltd based in the UK. We are a supplier of interior and exterior components to premium car manufacturers such as Corvel Ashby, Hadley Fenn, Marquist and Tavarelli. We would like to see a modern business card design that uses the colour blue.

Target Market(s)

Premium automotive car manufacturers.

Industry/Entity Type

Automotive

Contact Information for Business Card

Company Name : Velran Global Components Limited
Address: 17 Marlow Yard, Upper Heath, Warwick, CV31 8QL, United Kingdom
Web Address : www.velrancomponents-example.co.uk

Font styles to use
Other font styles liked:
• Helvetica

Colors
3176b5
0255a3
85acd3
cfdeed
cee9f5
85cae6
34a6d7
0692cd
9bcb3c

Requirements
Must have
• Clear company logo and a mixture of blue colours.
Nice to have
• A high quality modern image.
Should not have
• Multiple colours.

```html
<!DOCTYPE html>
<html lang="en">
<head>
<meta charset="utf-8">
<title>Velran Global Components – Business Card</title>
<link href="https://fonts.googleapis.com/css2?family=Arimo:wght@400;700&display=swap" rel="stylesheet">
<style>
  :root {
    --blue-main: #0692cd;
    --blue-back: #1e98d6;
    --blue-pattern: #2aa2dc;
    --green: #9bcb3c;
    --white: #ffffff;
    --stage: #e9edf1;
  }
  * { margin: 0; padding: 0; box-sizing: border-box; }
  html, body {
    width: 1200px; height: 900px; overflow: hidden;
    background: var(--stage);
    font-family: "Arimo", Helvetica, Arial, sans-serif;
  }
  .canvas {
    position: relative; width: 1200px; height: 900px;
    display: flex; flex-direction: column; align-items: center; justify-content: center; gap: 40px;
  }
  .card {
    position: relative; width: 640px; height: 366px; overflow: hidden;
    box-shadow: 0 6px 18px rgba(0,0,0,0.18);
  }
  .card-back { background: var(--blue-back); }
  .card-back .pattern-area {
    position: absolute; inset: 0;
    background: linear-gradient(135deg, var(--blue-pattern), var(--blue-back));
  }
  .card-back .back-name {
    position: absolute; right: 36px; bottom: 150px;
    color: var(--white); font-weight: 700; font-size: 14px; letter-spacing: 0.5px;
  }
  .card-front { background: var(--white); }
  .card-front svg.wave { position: absolute; inset: 0; }
  .brand {
    position: absolute; left: 38px; top: 100px;
    display: flex; align-items: center; gap: 10px;
  }
  .brand-square { width: 16px; height: 16px; background: var(--green); }
  .brand-name {
    color: var(--blue-main); font-weight: 700; font-size: 30px; letter-spacing: 0.3px;
  }
  .contact-list {
    position: absolute; right: 22px; top: 186px; list-style: none;
    color: var(--white); font-size: 12px; line-height: 19px; text-align: right;
  }
  .contact-list li { display: flex; align-items: center; justify-content: flex-end; gap: 8px; }
  .contact-list svg { width: 10px; height: 10px; fill: var(--green); flex: none; }
  .address {
    position: absolute; left: 40px; bottom: 22px;
    color: var(--white); font-size: 14px; line-height: 19px;
  }
</style>
</head>
<body>
<main class="canvas">
  <section class="card card-back">
    <div class="pattern-area" role="img" aria-label="Repeating brand pattern in light blue across the card back"></div>
    <span class="back-name">Velran Global Components</span>
  </section>

  <section class="card card-front">
    <svg class="wave" viewBox="0 0 640 366" preserveAspectRatio="none" aria-hidden="true">
      <path d="M0,226 C120,266 250,260 360,190 C450,135 550,115 640,108 L640,366 L0,366Z" fill="var(--green)"/>
      <path d="M0,235 C120,275 250,269 360,199 C450,144 550,124 640,117 L640,366 L0,366Z" fill="var(--white)"/>
      <path d="M0,238 C120,278 250,272 360,202 C450,147 550,127 640,120 L640,366 L0,366Z" fill="var(--blue-main)"/>
    </svg>

    <div class="brand">
      <span class="brand-square"></span>
      <span class="brand-name">Velran Global Components</span>
    </div>

    <ul class="contact-list">
      <li>780 555-0142
        <svg viewBox="0 0 10 10"><path d="M2 0.5 L4 0.5 L4.8 3 L3.6 4 C4.2 5.3 4.9 6 6 6.5 L7 5.3 L9.5 6 L9.5 8 C9.5 9 8.7 9.5 8 9.5 C4 9.2 0.8 6 0.5 2 C0.5 1.2 1.1 0.5 2 0.5Z"/></svg></li>
      <li>780 555-0187
        <svg viewBox="0 0 10 10"><rect x="2.5" y="0.5" width="5" height="9" rx="1"/></svg></li>
      <li>hello@velrancomponents-example.co.uk
        <svg viewBox="0 0 10 10"><path d="M0.5 2 L9.5 2 L9.5 8 L0.5 8Z"/></svg></li>
      <li>www.velrancomponents-example.co.uk
        <svg viewBox="0 0 10 10"><circle cx="5" cy="5" r="4.5"/></svg></li>
    </ul>

    <p class="address">17 Marlow Yard, Upper Heath<br>Warwick, CV31 8QL, UK</p>
  </section>
</main>
</body>
</html>
```